Brookmere Osteopathy flyer

I want a clean clear DL flyer (but also want an A4 poster) promoting a new Osteopathic business in a semi rural area in Tasmania (Australia).
It can have pictures like the examples attached to show people what Osteopathy is (its like Chiropractic and physiotherapy).
I am the sole practioner and am male, so any pictures would be best to be a white male if possible.
I've attached some wording, you can use all, or none of it
I don't have a phone number for the business yet
info@brookmereosteopathy.example
www.brookmereosteopathy.example
Target Market(s)
Australians, from tradies, professionals, babies to retired people
Industry/Entity Type
Health
Look and feel

```html
<!DOCTYPE html>
<html lang="en">
<head>
<meta charset="utf-8">
<title>Brookmere Osteopathy – DL Flyers</title>
<link rel="stylesheet" href="https://fonts.googleapis.com/css2?family=Mulish:wght@400;600;700&family=Oswald:wght@300&family=Saira+Condensed:wght@500;600;700&display=swap">
<style>
:root{
  --blue:#1a8ad0;
  --blue-band:#168bcc;
  --orange:#f39a32;
  --ink:#222;
  --paper:#ffffff;
  --stage:#eceae6;
  --mark-tint:#e3f0f9;
  --spine-tint:#dcebf6;
}
*{box-sizing:border-box;margin:0;padding:0}
html,body{width:1162px;height:1200px;overflow:hidden;background:var(--stage)}
.canvas{position:relative;width:1162px;height:1200px}
.flyer{position:absolute;top:107px;width:463px;height:985px;background:var(--paper);overflow:hidden;box-shadow:0 2px 8px rgba(0,0,0,.12)}
.flyer--front{left:93px}
.flyer--back{left:606px}

.header-band{position:absolute;left:0;top:0;width:100%;height:44px;background:var(--blue-band)}
.header-rule{position:absolute;left:0;right:0;top:46px;height:1.5px;background:var(--orange)}
.brand-mark{position:absolute;left:20px;top:17px;width:128px;height:128px;border-radius:50%;background:var(--mark-tint)}
.brand-name{position:absolute;left:161px;top:61px;font-family:'Mulish',sans-serif;font-weight:600;font-size:26.5px;line-height:31px;color:var(--blue);white-space:nowrap}

.intro{position:absolute;left:14px;top:154px;width:440px;font-family:'Mulish',sans-serif;font-size:16.3px;line-height:31px;color:var(--ink)}

.photo{position:absolute}
.photo--spine-model{left:0;top:295px;width:463px;height:276px;background:linear-gradient(120deg,#e4ebf0 0%,#eef2f4 50%,#dfe7ed 100%)}
.photo--infant{left:0;top:571px;width:226px;height:178px;background:linear-gradient(160deg,#9299b3 0%,#8490b3 100%)}
.photo--back-treatment{left:237px;top:571px;width:226px;height:178px;background:linear-gradient(110deg,#8fa6b3 0%,#d9c2ab 60%,#e8d3a6 100%)}
.photo--consult{left:0;top:164px;width:463px;height:309px;background:linear-gradient(100deg,#eeeeec 0%,#e7e9ea 55%,#e3c08f 85%,#d9aa66 100%)}

.service-area{position:absolute;left:19px;top:770px;font-family:'Mulish',sans-serif;font-weight:700;font-size:17.5px;color:var(--ink);white-space:nowrap}
.offer{position:absolute;left:19px;top:789px;font-family:'Saira Condensed',sans-serif;font-weight:700;font-size:32.5px;line-height:44px;color:var(--blue);white-space:nowrap}

.overlay-title{position:absolute;left:15px;top:250px;font-family:'Oswald',sans-serif;font-weight:300;font-size:38px;line-height:43px;letter-spacing:-.5px;color:#111;text-transform:uppercase}

.reasons-title{position:absolute;left:15px;top:484px;font-family:'Saira Condensed',sans-serif;font-weight:600;font-size:28px;color:var(--blue);white-space:nowrap}
.reasons{position:absolute;left:15px;top:528px;list-style:none}
.reasons li{display:flex;align-items:center;height:31.4px;font-family:'Mulish',sans-serif;font-size:16px;color:var(--ink);letter-spacing:.2px;white-space:nowrap}
.reasons svg{width:20px;height:14px;margin-right:15px;flex:none}

.spine-band{position:absolute;left:4px;top:866px;width:455px;height:62px;border-radius:60% 60% 10% 10%/100% 100% 20% 20%;background:linear-gradient(90deg,rgba(220,235,246,.2),var(--spine-tint) 45%,rgba(220,235,246,.4))}

.address{position:absolute;left:30px;top:938px;display:flex;align-items:center;font-family:'Mulish',sans-serif;font-size:23px;color:var(--ink);white-space:nowrap}
.address svg{width:22px;height:28px;margin-right:14px}
</style>
</head>
<body>
<div class="canvas">

  <section class="flyer flyer--front">
    <div class="header-band"></div>
    <div class="header-rule"></div>
    <div class="brand-mark"></div>
    <h1 class="brand-name">Brookmere Osteopathy<br>&amp; Dry Needling</h1>
    <p class="intro">Osteopaths Use A Combination of Joint Manipulation, Targeted Deep Tissue Massage And Stretching To Improve Function, Relieve Pain And Support The Body's Ability To Heal Itself.</p>
    <div class="photo photo--spine-model" role="img" aria-label="Practitioner pointing at a model spine and pelvis"></div>
    <div class="photo photo--infant" role="img" aria-label="Gentle hands cradling a sleeping baby's head"></div>
    <div class="photo photo--back-treatment" role="img" aria-label="Practitioner treating a patient's lower back"></div>
    <p class="service-area">Serving Semi Rural Area In Tasmania - Australia</p>
    <p class="offer">FREE INITIAL PHYSIO CONSULTATION</p>
    <div class="spine-band" role="img" aria-label="Faint spine decoration"></div>
    <p class="address">
      <svg viewBox="0 0 22 28"><path d="M11 1C5.5 1 1.5 5 1.5 10.3 1.5 17 11 27 11 27s9.5-10 9.5-16.7C20.5 5 16.5 1 11 1z" fill="#f39a32"/><circle cx="11" cy="10.3" r="4" fill="#fff"/></svg>
      48 Wattle Creek Road, Brookmere
    </p>
  </section>

  <section class="flyer flyer--back">
    <div class="header-band"></div>
    <div class="header-rule"></div>
    <div class="brand-mark"></div>
    <h1 class="brand-name">Brookmere Osteopathy<br>&amp; Dry Needling</h1>
    <div class="photo photo--consult" role="img" aria-label="Practitioner stretching a smiling patient's shoulder in a bright clinic"></div>
    <h2 class="overlay-title">Chiropractic<br>and<br>Physiotherapy</h2>
    <h3 class="reasons-title">Common Reasons People Visit An Osteopath</h3>
    <ul class="reasons">
      <li><svg viewBox="0 0 20 14"><path d="M1 13C2 7 6 4.5 12 4.5V1l7 5.5-7 5.5V8.5C7 8.5 3.5 10 1 13z" fill="#f39a32"/></svg>Back / Neck Pain</li>
      <li><svg viewBox="0 0 20 14"><path d="M1 13C2 7 6 4.5 12 4.5V1l7 5.5-7 5.5V8.5C7 8.5 3.5 10 1 13z" fill="#f39a32"/></svg>Headaches / Migraines</li>
      <li><svg viewBox="0 0 20 14"><path d="M1 13C2 7 6 4.5 12 4.5V1l7 5.5-7 5.5V8.5C7 8.5 3.5 10 1 13z" fill="#f39a32"/></svg>Joint And Muscle Pain</li>
      <li><svg viewBox="0 0 20 14"><path d="M1 13C2 7 6 4.5 12 4.5V1l7 5.5-7 5.5V8.5C7 8.5 3.5 10 1 13z" fill="#f39a32"/></svg>Pregnancy-related Discomfort</li>
      <li><svg viewBox="0 0 20 14"><path d="M1 13C2 7 6 4.5 12 4.5V1l7 5.5-7 5.5V8.5C7 8.5 3.5 10 1 13z" fill="#f39a32"/></svg>Disc Related Issues</li>
      <li><svg viewBox="0 0 20 14"><path d="M1 13C2 7 6 4.5 12 4.5V1l7 5.5-7 5.5V8.5C7 8.5 3.5 10 1 13z" fill="#f39a32"/></svg>Sciatica</li>
      <li><svg viewBox="0 0 20 14"><path d="M1 13C2 7 6 4.5 12 4.5V1l7 5.5-7 5.5V8.5C7 8.5 3.5 10 1 13z" fill="#f39a32"/></svg>Plantar Fasciitis</li>
      <li><svg viewBox="0 0 20 14"><path d="M1 13C2 7 6 4.5 12 4.5V1l7 5.5-7 5.5V8.5C7 8.5 3.5 10 1 13z" fill="#f39a32"/></svg>Tendonitis / Bursitis</li>
      <li><svg viewBox="0 0 20 14"><path d="M1 13C2 7 6 4.5 12 4.5V1l7 5.5-7 5.5V8.5C7 8.5 3.5 10 1 13z" fill="#f39a32"/></svg>Adhesive Capsulitis (Frozen Shoulder)</li>
      <li><svg viewBox="0 0 20 14"><path d="M1 13C2 7 6 4.5 12 4.5V1l7 5.5-7 5.5V8.5C7 8.5 3.5 10 1 13z" fill="#f39a32"/></svg>Tennis / Golfers Elbow</li>
    </ul>
    <div class="spine-band" role="img" aria-label="Faint spine decoration"></div>
    <p class="address">
      <svg viewBox="0 0 22 28"><path d="M11 1C5.5 1 1.5 5 1.5 10.3 1.5 17 11 27 11 27s9.5-10 9.5-16.7C20.5 5 16.5 1 11 1z" fill="#f39a32"/><circle cx="11" cy="10.3" r="4" fill="#fff"/></svg>
      48 Wattle Creek Road, Brookmere
    </p>
  </section>

</div>
</body>
</html>
```